Business Card Design & Gift cards, Gift Cert, Donation Card

Retail Gift Store-in addition to Business Cards we'd like sequenced 2 sided Gift cards, Gift Certificate Cards, and Donation Cards.please see examples and email for clarificationlogos attached with examples-
Gift Card, Gift Certificate and Donation Card will all be same style just differant upper right title, with back side info as example.
business card, as example is single sided.
looking for additional ideas for layout

Industry/Entity Type

Business

Contact Information for Business Card

211 Newman St.East Tawas, MI 48730989.362.8730Office@BrewKrew.com

Requirements
Must have
• Blue as per example
• Logos provided
• like gradiant background

```html
<!DOCTYPE html>
<html lang="en">
<head>
<meta charset="utf-8">
<title>Tillow Marsh – Business Card</title>
<link rel="stylesheet" href="https://fonts.googleapis.com/css2?family=Comic+Neue:wght@400;700&display=swap">
<style>
  :root {
    --page-bg: #e9ecf1;
    --royal-blue: #1c44e0;
    --band-blue: #0b3fe6;
    --frame-light: #b9cfe2;
    --sky-top: #cfe0f1;
    --sky-bottom: #a9c9ee;
    --back-top: #b3d0ee;
    --back-mid: #d6e6f3;
    --back-bottom: #9fc2e8;
    --ink-blue: #1235d6;
    --art-blue: #3a5fe0;
    --art-sun: #f4e04a;
    --white: #ffffff;
  }
  * { box-sizing: border-box; margin: 0; padding: 0; }
  html, body {
    width: 1200px; height: 892px; overflow: hidden;
    background: var(--page-bg);
    font-family: "Comic Neue", "Comic Sans MS", cursive;
  }
  .canvas {
    position: relative; width: 1200px; height: 892px;
    display: flex; justify-content: center; align-items: center; gap: 80px;
  }
  .card {
    width: 380px; height: 665px; position: relative;
    box-shadow: 0 8px 24px rgba(20, 40, 90, 0.18);
  }

  /* Front */
  .card-front {
    background: var(--royal-blue);
    padding: 16px;
  }
  .card-front .frame {
    width: 100%; height: 100%;
    border: 5px solid var(--frame-light);
    position: relative; overflow: hidden;
    background: linear-gradient(160deg, var(--sky-top), var(--sky-bottom));
  }
  .brand-name {
    position: absolute; top: 30px; left: 0; right: 0;
    text-align: center;
    font-weight: 700; font-size: 44px; letter-spacing: 1px;
    color: var(--ink-blue);
  }
  .band {
    position: absolute; left: 0; right: 0; top: 293px; bottom: 0;
    background: var(--band-blue);
  }
  .mascot-art {
    position: absolute; left: 62px; top: 98px;
    width: 224px; height: 250px; z-index: 2;
    border-radius: 14px;
    background: linear-gradient(170deg, var(--art-blue) 0%, #6f8fe8 55%, var(--art-sun) 100%);
    opacity: 0.85;
  }
  .contact {
    position: absolute; left: 20px; right: 20px; top: 84px;
    list-style: none; color: var(--white);
    font-weight: 700; font-size: 22px; line-height: 1.35; text-align: center;
  }

  /* Back */
  .card-back {
    background: linear-gradient(120deg, var(--back-top), var(--back-mid) 50%, var(--back-bottom));
    overflow: hidden;
  }
  .back-mascot-art {
    position: absolute; left: 40px; top: 30px;
    width: 150px; height: 150px; border-radius: 14px;
    background: linear-gradient(160deg, #8fb3ec, var(--back-mid));
    opacity: 0.6;
  }
  .back-name {
    position: absolute; top: 50%; left: 50%;
    transform: translate(-50%, -50%) rotate(90deg);
    white-space: nowrap;
    font-weight: 700; font-size: 84px; letter-spacing: 2px;
    color: var(--ink-blue);
  }
</style>
</head>
<body>
<main class="canvas">
  <section class="card card-front" aria-label="Business card front">
    <div class="frame">
      <h1 class="brand-name">Tillow Marsh</h1>
      <div class="mascot-art" role="img" aria-label="Illustration area: running stick figure on a rising yellow sun"></div>
      <div class="band">
        <ul class="contact">
          <li>989.517.4296</li>
          <li>Office@TillowMarsh.com</li>
          <li>482 Larkfield Ave.</li>
          <li>Harlow Bay, MI 48791</li>
        </ul>
      </div>
    </div>
  </section>

  <section class="card card-back" aria-label="Business card back">
    <div class="back-mascot-art" role="img" aria-label="Faint illustration area: running figure and sun"></div>
    <p class="back-name">Tillow Marsh</p>
  </section>
</main>
</body>
</html>
```